Event Center Website

We need a new website design for an upscale event center in Reno, Nevada. The building hosts everything from weddings to corporate events to funerals and it competitively more expensive. The overall look and feel is consistent with a Lake Tahoe aesthetic. The current site can be viewed at www.themaplehallevents.com. They are looking for a major upgrade. A sample site they like is www.cliffsidelodgestay.com. We have new photography available (some attached). The site should be very visual. A site map is attached as well for direction on what elements the site should include as well as labels for navigation. I am looking for a home page and sample interior page. Any questions, let me know. Thanks.
Updates

I have added some photography of the center itself for use rather than stock photography. Thanks!

Target Market(s)

Brides, professionals, high-income

Industry/Entity Type

Building

Requirements
Must have
• See site map

```html
<!DOCTYPE html>
<html lang="en">
<head>
<meta charset="utf-8">
<title>Meet Our Team – The Maple Hall</title>
<link rel="stylesheet" href="https://fonts.googleapis.com/css2?family=Ubuntu:wght@400;500;700&display=swap">
<style>
:root{
  --brown-dark:#4b2a17;
  --brown:#5a3318;
  --rust:#a8562a;
  --orange:#cf7a1e;
  --amber:#7d420d;
  --cream:#f5e7c6;
  --cream-light:#f1e8d6;
  --paper:#fbfaf8;
  --text:#2d1d12;
}
*{box-sizing:border-box;margin:0;padding:0}
html,body{width:1200px;height:945px;overflow:hidden}
body{position:relative;background:var(--paper);font-family:"Ubuntu",sans-serif;color:var(--text)}
.hero-band{position:absolute;left:0;top:0;width:1200px;height:157px;
  background:linear-gradient(180deg,#6b3f17 0%,#c5862e 45%,#8a5a2a 75%,#d9cbb4 100%)}
.util-nav{position:absolute;left:849px;top:0;width:227px;height:52px;background:var(--brown-dark);
  display:flex;align-items:center;justify-content:center;gap:22px;color:#fff;font-size:15px}
.util-nav .sep{width:1px;height:25px;background:#fff}
.main-nav{position:absolute;left:100px;top:52px;width:976px;height:58px;background:var(--cream);
  display:flex;align-items:center}
.brand{display:flex;align-items:center;gap:6px;margin-left:10px;width:190px;font-size:19px;font-weight:500;color:var(--brown-dark)}
.brand .dot{width:9px;height:9px;border-radius:50%;background:var(--rust)}
.main-nav ul{list-style:none;display:flex;gap:34px;margin-left:20px;font-size:14.5px;font-weight:500;color:var(--brown-dark)}
.title-band{position:absolute;left:0;top:157px;width:1200px;height:70px;background:var(--cream-light);border-bottom:2px solid var(--brown-dark)}
.title-band h2{position:absolute;left:124px;top:19px;font-size:26px;font-weight:500;color:var(--brown-dark)}
.crumbs{position:absolute;right:124px;top:27px;font-size:15.5px;font-weight:500;color:var(--brown-dark)}
.crumbs span{color:var(--rust)}
.section-title{position:absolute;left:0;top:252px;width:1200px;text-align:center;font-size:34px;font-weight:500;color:var(--brown-dark)}
.section-rule{position:absolute;left:563px;top:308px;width:75px;height:2px;background:var(--brown-dark)}
.member-name{position:absolute;left:124px;top:321px;font-size:26px;font-weight:500;color:var(--brown-dark)}
.member-role{position:absolute;left:124px;top:353px;font-size:22px;color:var(--rust)}
.member-rule{position:absolute;left:124px;top:388px;width:952px;height:2px;background:var(--brown-dark)}
.member-photo{position:absolute;left:124px;top:417px;width:382px;height:312px;border:2px solid var(--brown-dark);
  background:linear-gradient(180deg,#efefef 0%,#e6e1dc 55%,#3a3a40 100%)}
.member-bio{position:absolute;left:537px;top:412px;width:539px;font-size:13.2px;line-height:24.8px;text-align:justify;hyphens:auto;color:var(--text)}
.site-footer{position:absolute;left:0;top:778px;width:1200px;height:167px;background:var(--cream)}
.signup{position:absolute;left:131px;top:40px;width:340px;height:60px;background:var(--amber);display:flex;align-items:center;color:#fff}
.signup .field{flex:1;padding-left:9px;font-size:14.5px}
.signup svg{margin-right:10px}
.signup .send{width:56px;height:100%;background:var(--orange);display:flex;align-items:center;justify-content:center;font-size:14.5px}
.contact{position:absolute;left:494px;top:41px;width:375px;height:59px;background:#4a250c;border-radius:3px;display:flex;color:#fff;font-size:12.5px;white-space:nowrap}
.contact .addr{width:150px;padding:10px 0 0 12px;line-height:20px;border-right:1px solid #7a5030}
.contact .lines{padding:6px 0 0 9px;line-height:23px}
.contact .lines b{font-weight:400;color:var(--orange);margin-right:5px}
.social{position:absolute;left:887px;top:41px;width:189px;height:59px;background:#5a3318;border-radius:3px;
  display:flex;align-items:center;justify-content:center;gap:12px}
.social span{width:29px;height:29px;background:#d9b98a;border-radius:2px}
.footer-nav{position:absolute;left:0;top:128px;width:1200px;display:flex;justify-content:center;gap:28px;list-style:none;font-size:14px;color:var(--brown-dark)}
</style>
</head>
<body>
<div class="hero-band" role="img" aria-label="Banquet hall ceiling with draped fabric and chandelier"></div>
<div class="util-nav"><span>FAQ</span><span class="sep"></span><span>TESTIMONIAL</span></div>
<nav class="main-nav">
  <div class="brand"><span class="dot"></span>The Maple Hall</div>
  <ul><li>ABOUT US</li><li>GALLERY</li><li>WEDDING</li><li>MEETINGS</li><li>OTHER EVENTS</li><li>CATERING</li><li>MENUS</li></ul>
</nav>
<header class="title-band">
  <h2>MEET OUR TEAM</h2>
  <div class="crumbs">HOME / <span>MEET OUR TEAM</span></div>
</header>
<main>
  <h1 class="section-title">Meet Our Team</h1>
  <div class="section-rule"></div>
  <h3 class="member-name">Dana</h3>
  <p class="member-role">General Manager</p>
  <div class="member-rule"></div>
  <div class="member-photo" role="img" aria-label="Portrait of the general manager in a dark suit"></div>
  <p class="member-bio">Dana grew up in Reno and has many ties to the Reno community. Her love for event planning and becoming a “foodie” started many years ago when she became Event Director and Assistant Manager at The Ridgeview Club. Planning events and creating menus became a passion and has followed her throughout her career. Having been a part of event planning, catering and management for more than two decades, The Maple Hall is the perfect fit for Dana. Her philosophy for managing a successful venue is creating a professional, inviting atmosphere where guests will enjoy amazing food served by welcoming staff. Dana’s team shares a passion for food and quality of service. They want to ensure that every event is special and successful. Their goal is create the perfect setting for a memorable event. Dana is also the Director of Sales and loves working with our clients. Planning a fun fashion show, a birthday bash or an elegant wedding, every affair is a new adventure. Dana enjoys watching an event progress from ideas on a piece of paper to an amazing party. Dana and her husband love to travel since they became empty nesters.</p>
</main>
<footer class="site-footer">
  <div class="signup">
    <span class="field">ENTER YOUR EMAIL</span>
    <svg width="32" height="30" viewBox="0 0 32 30"><path d="M2 12 L16 2 L30 12 V28 H2 Z" fill="#fff"/><path d="M2 12 L16 21 L30 12 M2 28 L13 19 M30 28 L19 19" stroke="#7d420d" stroke-width="1.5" fill="none"/><circle cx="16" cy="10" r="3.5" fill="none" stroke="#7d420d" stroke-width="1.3"/></svg>
    <span class="send">SEND</span>
  </div>
  <div class="contact">
    <div class="addr">48 Aspen Ridge Road<br>Reno, NV 89511</div>
    <div class="lines"><div><b>Phone:</b>775-555-0142</div><div><b>Email:</b>info@themaplehallevents.com</div></div>
  </div>
  <div class="social"><span></span><span></span><span></span><span></span></div>
  <ul class="footer-nav"><li>ABOUT US</li><li>GALLERY</li><li>WEDDING</li><li>MEETINGS</li><li>OTHER EVENTS</li><li>CATERING</li><li>MENUS</li></ul>
</footer>
</body>
</html>
```